brightwell - Property Management DL Card

I am after a savvy designer to cut through junk mail! so many real estate agents use flyers to promote themselves and their business and usually sales. We are a property management firm (residential) and we want to represent landlords that have existing investment properties and need a quality agent to represent them. Can you help?
DL size, will be printed and delivered to mailboxes. For a look at our website go to www.brightwellrs.com.au. Keep it simple and clutter free.
it is to be double sided - with one side to be simple and clear - just our website, logo and telephone number on the back.
attached is our logo and our telephone number is 1300 48 92 16
the above are 2 essential elements to be included + our email address: admin@brightwellrs.com.au
also attached are our transparent price list

Target Market(s)
property investors,
people that manage properties themselves
Industry/Entity Type
Property Management
- arial
Look and feel

```html
<!DOCTYPE html>
<html lang="en">
<head>
<meta charset="utf-8">
<title>brightwell – Property Management DL Card</title>
<link rel="stylesheet" href="https://fonts.googleapis.com/css2?family=Arimo:wght@400;700&display=swap">
<style>
  :root {
    --canvas: #ececec;
    --card: #ffffff;
    --ink: #111111;
    --brand: #2b2b2b;
    --muted: #c6c6c6;
    --grey-light: #a8a8aa;
    --grey-dark: #3b3b3d;
    --photo-warm-a: #efe4d2;
    --photo-warm-b: #b49a78;
    --photo-cool-a: #f4f2ee;
    --photo-cool-b: #8e8a84;
  }
  * { margin: 0; padding: 0; box-sizing: border-box; }
  html, body { width: 1200px; height: 900px; overflow: hidden; }
  body {
    background: var(--canvas);
    font-family: "Arimo", Arial, sans-serif;
    color: var(--ink);
    position: relative;
  }
  .card {
    position: absolute;
    background: var(--card);
    overflow: hidden;
    box-shadow: 0 2px 8px rgba(0,0,0,0.18);
  }
  .card-front { left: 18px; top: 16px; width: 950px; height: 433px; }
  .card-back  { left: 234px; top: 459px; width: 947px; height: 434px; }
  .card-shapes { position: absolute; inset: 0; width: 100%; height: 100%; }
  .brand-name {
    position: absolute;
    font-weight: 400;
    font-size: 54px;
    letter-spacing: 0.5px;
    color: var(--brand);
    line-height: 1;
  }
  .card-front .brand-name { left: 148px; top: 36px; }
  .card-back .brand-name  { left: 561px; top: 22px; }
  .headline {
    position: absolute;
    font-weight: 700;
    font-size: 28px;
    line-height: 1;
    white-space: nowrap;
  }
  .card-front .headline { left: 10px; top: 207px; }
  .card-back .headline  { left: 475px; top: 175px; }
  .intro {
    position: absolute;
    left: 12px; top: 246px; width: 510px;
    font-size: 13px; line-height: 1.35;
    text-align: center;
  }
  .call-label {
    position: absolute; left: 164px; top: 362px;
    font-size: 23px; font-weight: 700; line-height: 1; color: var(--muted);
  }
  .call-number {
    position: absolute; left: 117px; top: 390px;
    font-size: 37px; font-weight: 700; line-height: 1; letter-spacing: 0.5px;
  }
  .contact-list { position: absolute; left: 528px; top: 304px; list-style: none; }
  .contact-item {
    display: flex; align-items: center; gap: 6px;
    font-size: 18px; height: 43px;
  }
  .contact-icon { width: 24px; height: 24px; }
</style>
</head>
<body>

<section class="card card-front">
  <svg class="card-shapes" viewBox="0 0 810 369" preserveAspectRatio="none">
    <defs>
      <linearGradient id="interiorWarm" x1="0" y1="0" x2="1" y2="1">
        <stop offset="0" stop-color="var(--photo-warm-a)"/>
        <stop offset="1" stop-color="var(--photo-warm-b)"/>
      </linearGradient>
    </defs>
    <polygon points="400,0 730,0 470,128" fill="var(--grey-light)"/>
    <polygon points="738,0 810,0 810,190" fill="var(--grey-dark)"/>
    <polygon points="458,146 726,10 810,198 810,282 672,369 598,369" fill="url(#interiorWarm)" role="img" aria-label="Photo of a bright modern living and dining room with staircase"/>
    <polygon points="684,369 810,290 810,369" fill="var(--grey-light)"/>
  </svg>
  <div class="brand-name">brightwell</div>
  <h1 class="headline">We Specialise In Property Management</h1>
  <p class="intro">Are you a property owner, private landlord, Mum/Dad investor or developer looking for<br>for quality property management to represent you? brightwell is the company to contact!</p>
  <div class="call-label">Cal Us Today:</div>
  <div class="call-number">1300 48 92 16</div>
</section>

<section class="card card-back">
  <svg class="card-shapes" viewBox="0 0 808 370" preserveAspectRatio="none">
    <defs>
      <linearGradient id="interiorCool" x1="0" y1="0" x2="1" y2="1">
        <stop offset="0" stop-color="var(--photo-cool-a)"/>
        <stop offset="1" stop-color="var(--photo-cool-b)"/>
      </linearGradient>
    </defs>
    <polygon points="0,0 205,0 0,112" fill="var(--grey-light)"/>
    <polygon points="0,124 222,4 278,4 400,258 400,300 168,370 0,370" fill="url(#interiorCool)" role="img" aria-label="Photo of a white living room with sofa and tall windows"/>
    <polygon points="0,172 0,370 58,370" fill="var(--grey-dark)"/>
    <polygon points="180,370 410,262 410,370" fill="var(--grey-light)"/>
  </svg>
  <div class="brand-name">brightwell</div>
  <h2 class="headline">Competitive Fees For All Budgets</h2>
  <ul class="contact-list">
    <li class="contact-item">
      <svg class="contact-icon" viewBox="0 0 24 24" fill="none" stroke="var(--ink)" stroke-width="1.6">
        <circle cx="12" cy="12" r="10.5"/>
        <path d="M8.5 6.5l2 2.5-1.2 1.5c.8 1.8 2.2 3.2 4 4l1.5-1.2 2.5 2-1.2 1.8c-4.5-.3-8.6-4.4-9-9z"/>
      </svg>
      <span>1300 48 92 16</span>
    </li>
    <li class="contact-item">
      <svg class="contact-icon" viewBox="0 0 24 24" fill="none" stroke="var(--ink)" stroke-width="1.6">
        <circle cx="12" cy="12" r="10.5"/>
        <rect x="6" y="8" width="12" height="8"/>
        <path d="M6 8l6 4.5L18 8"/>
      </svg>
      <span>admin@brightwellrs.com.au</span>
    </li>
    <li class="contact-item">
      <svg class="contact-icon" viewBox="0 0 24 24" fill="none" stroke="var(--ink)" stroke-width="1.4">
        <circle cx="12" cy="12" r="10.5"/>
        <ellipse cx="12" cy="12" rx="4.5" ry="10.5"/>
        <path d="M1.5 12h21M3.5 7h17M3.5 17h17"/>
      </svg>
      <span>www.brightwellrs.com.au</span>
    </li>
  </ul>
</section>

</body>
</html>
```